Sale- Bundle signs

We are looking for a design to use for Permanent SALE/Bundle deal signs. We are a natural bath products company who uses all natural ingredients to create our handmade line of natural products. We love a clean, fresh look and feel. Simple eye-catching that will be a quick glance and they will know the offer.
We would like to have something simple, eye catching that will promote sales on our different products.
Dead Sea Salt Body Scrubs
large 2 for $40
small 3 for $20
Moisturizing Wash with coconut & olive oil
2 for $20
There are several more needed but we are hoping to decide on one template before making all of the signs.
Visit our website here www.tamberlinewash.com
Target Market(s)
Our store serves 70% women and the majority of our customers are 30+ years old.
Industry/Entity Type
It Company
Other font styles liked:
- Century Gothic or similar
Look and feel
Each slider illustrates characteristics of the customer's brand and the style your logo design should communicate.

```html
<!DOCTYPE html>
<html lang="en">
<head>
<meta charset="utf-8">
<title>Verdelle – Bundle Sale Sign</title>
<link rel="stylesheet" href="https://fonts.googleapis.com/css2?family=Questrial&family=Mulish:wght@800&display=swap">
<style>
  :root {
    --backdrop: #0b0c0e;
    --sign-white: #ffffff;
    --sign-butter: #fdf7a6;
    --sign-aqua: #8ccfc3;
    --brand-green: #587d2f;
    --tagline-green: #4f6a34;
    --teal-panel: #35ae9a;
    --orange-panel: #e58745;
    --price-yellow: #fdf39a;
    --heading-white: #ffffff;
    --stone-dark: #2b2c2e;
    --stone-mid: #5a5c5f;
  }
  * { margin: 0; padding: 0; box-sizing: border-box; }
  html, body {
    width: 1200px; height: 1000px; overflow: hidden;
    background: var(--backdrop);
  }
  .sign {
    position: absolute; left: 280px; top: 50px;
    width: 642px; height: 900px; overflow: hidden;
    background: linear-gradient(160deg,
      var(--sign-white) 0%, var(--sign-white) 22%,
      var(--sign-butter) 55%, var(--sign-butter) 68%,
      var(--sign-aqua) 100%);
  }
  .brand {
    position: absolute; left: 0; right: 0; top: 20px;
    text-align: center; font-family: "Questrial", sans-serif;
  }
  .brand-name {
    font-size: 104px; line-height: 1; color: var(--brand-green);
    letter-spacing: 2px;
  }
  .brand-tagline {
    margin-top: 4px; font-size: 33px; line-height: 1.2; letter-spacing: 2px;
    color: var(--tagline-green);
  }
  .offer {
    position: absolute; left: 66px; width: 509px;
    text-align: center;
  }
  .offer-scrubs { top: 191px; height: 280px; background: var(--teal-panel); padding-top: 52px; }
  .offer-wash { top: 471px; height: 293px; background: var(--orange-panel); padding-top: 37px; }
  .offer-title {
    font-family: "Questrial", sans-serif; font-weight: 400;
    font-size: 26px; line-height: 1.3;
    color: var(--heading-white); letter-spacing: 0.5px;
  }
  .offer-price {
    font-family: "Mulish", sans-serif; font-weight: 800;
    font-size: 58px; line-height: 68px; color: var(--price-yellow);
  }
  .offer-scrubs .offer-title { margin-bottom: 11px; }
  .offer-wash .offer-title { line-height: 1.5; }
  .offer-wash .offer-price { margin-top: 4px; }
  .spa-stones {
    position: absolute; left: 0; top: 655px; width: 290px; height: 245px;
    background: radial-gradient(ellipse closest-side at 40% 50%,
      var(--stone-mid) 0%, var(--stone-dark) 55%, rgba(43,44,46,0) 100%);
  }
</style>
</head>
<body>
  <main class="sign">
    <header class="brand">
      <div class="brand-name">Verdelle</div>
      <div class="brand-tagline">NATURAL BATH PRODUCTS</div>
    </header>

    <section class="offer offer-scrubs">
      <h2 class="offer-title">DEAD SEA SALT BODY SCRUBS</h2>
      <p class="offer-price">Large 2 for $40</p>
      <p class="offer-price">Small 3 for $20</p>
    </section>

    <section class="offer offer-wash">
      <h2 class="offer-title">MOISTURIZING WASH WITH<br>COCONUT &amp; OLIVE OIL</h2>
      <p class="offer-price">2 for $20</p>
    </section>

    <div class="spa-stones" role="img" aria-label="Wet black spa stones with a white frangipani flower and water droplets"></div>
  </main>
</body>
</html>
```